Create modern and sleek business card for luxury real estate company

We're a "boutique" real estate office looking for a design that gets across a highly modern luxury brand. Blacks and whites are probably the best colors unless we try a silver foil for the logo. I've attached a version of our current logo here. I'd like to swap out the current font on there with Gotham Light Regular.

I'm looking to have one side of the card have the logo with the space for our agents info on the other side.

Target Market(s)

Young professionals in a "luxury" headspace

Industry/Entity Type

Real estate

Contact Information for Business Card

A place for agent name, cell number, website. The slogan "Simply Rethinking Real Estate".

Font styles to use
Other font styles liked:
• Gotham Regular

Colors

Designer to choose only greyscale colors for use in the design.

Requirements
Must have
• Matte black as the background color. Clean lines and use of contrast. A specific design aspect that will use silver foil.
Nice to have
• Up in the air on integrating a QR code
Should not have
• Any houses or other real estate related design (ex: a clip art house)

```html
<!DOCTYPE html>
<html lang="en">
<head>
<meta charset="utf-8">
<title>Verity Estates — Business Card</title>
<link href="https://fonts.googleapis.com/css2?family=Open+Sans:wght@300;400;600;700&display=swap" rel="stylesheet">
<style>
  :root {
    --stage: #4a4a4c;
    --card: #0e0e0f;
    --ink: #f2f2f2;
    --silver: #d9d9d9;
    --muted: #8a8a8a;
    --rule: #6b6b6b;
  }
  * { box-sizing: border-box; margin: 0; padding: 0; }
  html, body {
    width: 1200px; height: 801px; overflow: hidden;
    background: var(--stage);
    font-family: "Open Sans", Arial, sans-serif;
  }
  .stage {
    width: 1200px; height: 801px;
    display: flex; align-items: center; justify-content: center; gap: 48px;
  }
  .card {
    width: 525px; height: 300px;
    background: var(--card);
    border-radius: 3px;
    box-shadow: 0 14px 30px rgba(0,0,0,.35);
    position: relative;
  }
  /* Agent side */
  .card-agent { display: flex; align-items: center; }
  .agent-identity {
    width: 240px; text-align: right; padding-right: 26px;
  }
  .agent-name {
    color: var(--ink); font-weight: 700; font-size: 19px; letter-spacing: .06em;
  }
  .agent-title {
    color: var(--muted); font-weight: 400; font-size: 14px; margin-top: 2px;
  }
  .divider {
    width: 1px; height: 72px; background: var(--rule);
  }
  .contact-list {
    list-style: none; padding-left: 22px;
  }
  .contact-item {
    display: flex; align-items: center; gap: 8px;
    color: var(--silver); font-size: 14px; font-weight: 400; line-height: 1.55;
  }
  .contact-icon { width: 11px; height: 11px; flex: none; }
  /* Brand side */
  .card-brand {
    display: flex; align-items: center; justify-content: center; gap: 22px;
  }
  .brand-disc {
    width: 92px; height: 92px; border-radius: 50%;
    border: 3px solid var(--silver);
  }
  .brand-name {
    color: var(--silver); font-weight: 400; font-size: 44px;
    letter-spacing: .04em; line-height: 1.05; text-transform: uppercase;
  }
</style>
</head>
<body>
<main class="stage">
  <section class="card card-agent" aria-label="Agent side">
    <div class="agent-identity">
      <p class="agent-name">ADRIAN COLBERT</p>
      <p class="agent-title">President</p>
    </div>
    <span class="divider"></span>
    <ul class="contact-list">
      <li class="contact-item">
        <svg class="contact-icon" viewBox="0 0 12 12" aria-hidden="true"><circle cx="6" cy="6" r="6" fill="#d9d9d9"/><path d="M3.6 3.2l1.2-.3.6 1.5-.7.5c.4.8 1 1.4 1.8 1.8l.5-.7 1.5.6-.3 1.2C6 7.9 4 6 3.6 3.2z" fill="#0e0e0f"/></svg>
        555-012-4890
      </li>
      <li class="contact-item">
        <svg class="contact-icon" viewBox="0 0 12 12" aria-hidden="true"><rect x="0.5" y="2" width="11" height="8" rx="1" fill="#d9d9d9"/><path d="M1 2.6l5 3.6 5-3.6" stroke="#0e0e0f" stroke-width="1" fill="none"/></svg>
        hello@verityestates.com
      </li>
      <li class="contact-item">
        <svg class="contact-icon" viewBox="0 0 12 12" aria-hidden="true"><circle cx="6" cy="6" r="5.5" fill="#d9d9d9"/><path d="M.5 6h11M6 .5c-2.4 2.8-2.4 8.2 0 11M6 .5c2.4 2.8 2.4 8.2 0 11" stroke="#0e0e0f" stroke-width=".9" fill="none"/></svg>
        www.verityestates.com
      </li>
    </ul>
  </section>

  <section class="card card-brand" aria-label="Brand side">
    <span class="brand-disc" aria-hidden="true"></span>
    <p class="brand-name">Verity<br>Estates</p>
  </section>
</main>
</body>
</html>
```